Fast quick flyer for Merchant Growth Fair

I am an information security consultant that needs to have a flyer and QUICK!!!
I need to get it to the printer today to have if done by monday. Quick turnaound.
I don't need the most amazing flyer but something that will capture their attention and offer them 40% off my base rate.
Updates

Here's some slight updates to the text, can you update and incorporate (PS: For some reason, when I initially put in Vantrel Systems, a " (quote) showed up, it's an apostrophe ( Vantrel Systems): Text: Vantrel Systems is the information security department for small and mid-sized businesses. Leveraging our 20+ years of information security experience, we will bring you the same level of service found at Pinnacle 300 companies. Small and mid-sized companies are often the target of malicious activity because they tend to lack the expertise to properly secure their environments. Now you can have your very own information security department at a fraction of the cost of a full time staff. Our typical rate for our premium offering: Guardline Plus is $5000/month based on a signed one year commitment. But for expo attendees, we are offering a special discount. As an expo attendee, you are eligible for a 40% discount. Guardline Plus for expo attendees will be $3000/month based on a signed one year commitment. Why put your company and your business at risk. Vantrel Systems is here to secure your company's future! Contact us now for more information: Leon Whitcombe Vantrel Systems "The information security department of small and mid-sized companies" 555-318-7292 info@vantrelsys.example http://www.vantrelsys.example

Also, this is going to be a 6x9 heavy stock postcard

Addition: Promo Code: GrowthFair 2014

Target Market(s)

Small businesses with a small IT department that can't afford to hire a full time IT Security Staff. We are the outsourced Information Security group

Industry/Entity Type

Small Business

Colors

Designer to choose colors to be used in the design.

Requirements
Must have
• Sell the idea that they need to take security serious and that we are the ones to do the job

Should stress that because they are attendees of the Merchant Growth Fair, they are eligible to get a 40% discount on our standard rate

```html
<!DOCTYPE html>
<html lang="en">
<head>
<meta charset="utf-8">
<title>Vantrel Systems – Merchant Growth Fair Offer</title>
<link rel="stylesheet" href="https://fonts.googleapis.com/css2?family=Mulish:wght@400;600;700;800&display=swap">
<style>
  :root {
    --teal: #1fb5c6;
    --teal-light: #4fd0dd;
    --teal-dark: #0f8d9a;
    --navy: #1f2a4a;
    --ink: #111;
    --white: #fff;
    --bg-center: #ffffff;
    --bg-edge: #d6d8da;
  }
  * { margin: 0; padding: 0; box-sizing: border-box; }
  html, body { width: 927px; height: 1200px; overflow: hidden; }
  body {
    position: relative;
    font-family: "Mulish", "Century Gothic", sans-serif;
    color: var(--ink);
    background: radial-gradient(circle at 50% 62%, var(--bg-center) 0%, #f1f2f3 35%, var(--bg-edge) 100%);
  }

  .offer-card {
    position: absolute; left: 144px; top: 93px; width: 649px; height: 613px;
    background: var(--white);
    border: 6px solid var(--teal-light);
    border-radius: 14px;
    box-shadow: 0 0 0 1px var(--teal), 0 6px 14px rgba(0,0,0,.12);
  }

  .ribbon-tab { position: absolute; left: 134px; top: 148px; width: 100px; height: 86px; z-index: 2; }

  .brand { position: absolute; left: 96px; top: 50px; display: flex; align-items: center; gap: 18px; }
  .brand-mark { width: 70px; height: 70px; background: var(--navy); }
  .brand-name {
    font-weight: 400; font-size: 44px; line-height: 42px; letter-spacing: 1px;
    color: var(--navy); text-transform: uppercase;
  }

  .offer-copy {
    position: absolute; left: 30px; top: 177px; width: 584px;
    font-size: 17.4px; line-height: 22.7px; letter-spacing: .25px;
  }
  .offer-copy p + p { margin-top: 22.7px; }
  .offer-copy strong { font-weight: 700; }

  .promo-code {
    position: absolute; right: 30px; top: 548px;
    font-size: 18px; font-weight: 800; color: var(--teal-dark); letter-spacing: .3px;
  }

  .discount-badge { position: absolute; left: 80px; top: 640px; width: 200px; height: 220px; }
  .badge-text {
    position: absolute; left: 88px; top: 669px; width: 176px;
    text-align: center; color: var(--white); text-transform: uppercase;
  }
  .badge-text .small { font-size: 16.5px; line-height: 20px; }
  .badge-text .big { font-size: 72px; font-weight: 600; line-height: 64px; letter-spacing: -3px; margin: 2px 0 0; }

  .contact-box {
    position: absolute; left: 30px; top: 878px; width: 466px; height: 233px;
    background: var(--teal); border-radius: 12px; overflow: hidden;
    color: var(--white); text-align: center;
    box-shadow: 0 14px 16px -10px rgba(0,0,0,.35);
  }
  .contact-lead { margin-top: 15px; font-size: 20px; }
  .contact-name { margin-top: 12px; font-weight: 800; font-size: 20px; line-height: 25px; text-transform: uppercase; }
  .contact-tagline { margin-top: 8px; font-size: 19.5px; line-height: 23px; }
  .contact-band {
    position: absolute; left: 0; bottom: 0; width: 100%; height: 71px;
    background: var(--teal-dark); border-top: 1.5px dashed rgba(255,255,255,.8);
    display: flex; align-items: center;
  }
  .contact-phone { width: 186px; font-weight: 800; font-size: 21px; }
  .contact-web {
    height: 56px; border-left: 1.5px dashed rgba(255,255,255,.8);
    padding-left: 20px; text-align: left; font-weight: 700; font-size: 15.5px; line-height: 23px;
    display: flex; flex-direction: column; justify-content: center;
  }

  .office-scene { position: absolute; left: 482px; top: 705px; width: 445px; height: 495px; }
</style>
</head>
<body>
  <section class="offer-card">
    <div class="brand">
      <span class="brand-mark"></span>
      <span class="brand-name">Vantrel<br>Systems</span>
    </div>
    <div class="offer-copy">
      <p><strong>Vantrel Systems</strong> is the information security department for small and mid-sized businesses. Leveraging our <strong>20+ years</strong> of information security experience, we will bring you the same level of service found at Pinnacle 300 companies. Small and mid-sized companies are often the target of malicious activity because they tend to lack the expertise to properly secure their environments. Now you can have your very own information security department at a fraction of the cost of a full time staff.</p>
      <p>Our typical rate for our premium offering: Guardline Plus is <strong>$5000/month</strong> based on a signed one year commitment. But for expo attendees, we are offering a special discount. As an expo attendee, you are eligible for a <strong>40% discount</strong>. Guardline Plus for expo attendees will be <strong>$3000/month</strong> based on a signed one year commitment. Why put your company and your business at risk. <strong>Vantrel Systems</strong> is here to secure your company’s future!</p>
    </div>
    <p class="promo-code">Promo Code: GrowthFair 2014</p>
  </section>

  <svg class="ribbon-tab" viewBox="0 0 100 86" aria-hidden="true">
    <defs>
      <linearGradient id="tabFill" x1="0" y1="0" x2="1" y2="0">
        <stop offset="0" stop-color="#0f8d9a"/><stop offset="1" stop-color="#4fd0dd"/>
      </linearGradient>
    </defs>
    <polygon points="0,8 10,0 10,12" fill="#0b6e78"/>
    <polygon points="0,8 62,8 98,44 62,80 0,80" fill="url(#tabFill)"/>
  </svg>

  <svg class="discount-badge" viewBox="0 0 200 220" aria-hidden="true">
    <polygon points="150,150 184,213 110,180" fill="#fff"/>
    <circle cx="96" cy="97" r="90" fill="#fff"/>
    <polygon points="146,148 172,200 116,172" fill="#1fb5c6"/>
    <circle cx="96" cy="97" r="77" fill="#1fb5c6"/>
  </svg>
  <div class="badge-text">
    <div class="small">You are<br>eligible for a</div>
    <div class="big">40%</div>
    <div class="small">Discount.</div>
  </div>

  <section class="contact-box">
    <p class="contact-lead">Contact us now for more information:</p>
    <p class="contact-name">Leon Whitcombe<br>Vantrel Systems</p>
    <p class="contact-tagline">“The information security department<br>of small and mid-sized companies”</p>
    <div class="contact-band">
      <span class="contact-phone">555-318-7292</span>
      <span class="contact-web"><span>info@vantrelsys.example</span><span>http://www.vantrelsys.example</span></span>
    </div>
  </section>

  <svg class="office-scene" viewBox="0 0 445 495" role="img" aria-label="Illustration of a glass office building with trees and shrubs in front">
    <defs>
      <linearGradient id="sceneFill" x1="0" y1="0" x2="0.6" y2="1">
        <stop offset="0" stop-color="#4fd0dd" stop-opacity="0"/>
        <stop offset="0.35" stop-color="#4fd0dd" stop-opacity="0.55"/>
        <stop offset="1" stop-color="#1fb5c6"/>
      </linearGradient>
    </defs>
    <rect x="0" y="0" width="445" height="495" fill="url(#sceneFill)"/>
  </svg>
</body>
</html>
```